Business Card for Coastal Tundrabridge Advisory

We need a business card for Coastal Tundrabridge Advisory. The company website address is provided below. The company logo is attached. We provide specialized permafrost services to the mining, transportation, and oil & gas industries. The card should be prepared for:
Matthias Korhonen, PhD.
Coastal Tundrabridge Advisory
PO Box 418259
Quillwater, Alaska 99642
Direct: +1-907-555-0143
Email: mkorhonen@tundrabridgeadvisory.example
Website: www.coastaltundrabridgeadvisory.example

```html
<!DOCTYPE html>
<html lang="en">
<head>
<meta charset="utf-8">
<title>Coastal Tundrabridge Advisory – Business Card</title>
<link rel="stylesheet" href="https://fonts.googleapis.com/css2?family=Montserrat:wght@400;500;600;700&display=swap">
<style>
  :root {
    --stage: #d8d4cd;
    --paper: #ffffff;
    --ink: #1b222a;
    --band-dark: #333234;
    --band-grey: #6b6b6b;
    --back-dark: #222222;
    --light: #ffffff;
    --muted-light: #e6e6e6;
  }
  html, body {
    margin: 0;
    padding: 0;
    width: 900px;
    height: 1200px;
    overflow: hidden;
    background: var(--stage);
    font-family: "Montserrat", Arial, sans-serif;
  }
  .card {
    position: absolute;
    left: 80px;
    width: 742px;
    height: 440px;
    border-radius: 30px;
    overflow: hidden;
    box-shadow: 0 6px 14px rgba(0,0,0,0.25);
  }
  .card--front { top: 132px; background: var(--paper); color: var(--ink); }
  .card--back { top: 638px; background: var(--back-dark); color: var(--light); }

  .brand {
    position: absolute;
    font-weight: 700;
    text-transform: uppercase;
    line-height: 1;
    margin: 0;
  }
  .brand__line1 { display: block; font-size: 38px; letter-spacing: 1px; }
  .brand__line2 { display: block; font-size: 17px; letter-spacing: 8px; margin-top: 12px; }
  .card--front .brand { left: 56px; top: 52px; color: var(--ink); }
  .card--back .brand { left: 0; right: 0; top: 180px; text-align: center; color: var(--light); }

  .holder { position: absolute; left: 30px; top: 182px; }
  .holder__name { margin: 0; font-size: 26px; font-weight: 700; letter-spacing: 0.2px; }
  .holder__title { margin: 4px 0 0 1px; font-size: 16px; font-weight: 400; }

  .band { position: absolute; left: 0; top: 0; }

  .contact {
    position: absolute;
    left: 46px;
    top: 273px;
    margin: 0;
    padding: 0;
    list-style: none;
    color: var(--light);
    font-size: 16px;
  }
  .contact__item { display: flex; align-items: center; height: 22.5px; }
  .contact__icon { width: 14px; height: 14px; margin-right: 10px; fill: var(--light); }

  .address {
    position: absolute;
    left: 42px;
    top: 374px;
    margin: 0;
    font-style: normal;
    font-size: 16px;
    line-height: 22px;
  }
</style>
</head>
<body>
  <section class="card card--front" aria-label="Card front">
    <svg class="band" width="742" height="440" viewBox="0 0 742 440" aria-hidden="true">
      <polygon points="0,255 512,255 462,358 0,358" fill="var(--band-dark)"/>
      <polygon points="522,255 742,255 742,358 470,358" fill="var(--band-grey)"/>
    </svg>

    <h1 class="brand">
      <span class="brand__line1">Coastal Tundrabridge</span>
      <span class="brand__line2">Advisory</span>
    </h1>

    <div class="holder">
      <h2 class="holder__name">Matthias Korhonen, PhD.</h2>
      <p class="holder__title">CEO &amp; Founder</p>
    </div>

    <ul class="contact">
      <li class="contact__item">
        <svg class="contact__icon" viewBox="0 0 16 16" aria-hidden="true"><path d="M3 5c0-2 2-3 5-3s5 1 5 3v1h-3V5H6v1H3zM4 7h8l2 7H2z M8 9a2 2 0 1 0 0.01 0z"/></svg>
        +1-907-555-0143
      </li>
      <li class="contact__item">
        <svg class="contact__icon" viewBox="0 0 16 16" aria-hidden="true"><path d="M1 3h14v10H1z" /><path d="M1 3l7 6 7-6" fill="none" stroke="#333234" stroke-width="1.4"/></svg>
        mkorhonen@tundrabridgeadvisory.example
      </li>
      <li class="contact__item">
        <svg class="contact__icon" viewBox="0 0 16 16" aria-hidden="true"><circle cx="8" cy="8" r="7"/><path d="M4 5c2 0 3 1 2 3s1 3 0 5M10 3c-1 2 1 3 3 3" fill="none" stroke="#333234" stroke-width="1.3"/></svg>
        www.coastaltundrabridgeadvisory.example
      </li>
    </ul>

    <address class="address">
      PO Box 418259<br>
      Quillwater, Alaska 99642
    </address>
  </section>

  <section class="card card--back" aria-label="Card back">
    <p class="brand">
      <span class="brand__line1">Coastal Tundrabridge</span>
      <span class="brand__line2">Advisory</span>
    </p>
  </section>
</body>
</html>
```